Our new beauty salon requires a price list brochure

Our beauty clinic is a medical grade skin care clinic. So our salon is very clinical and professional in appearance. I would like the colours to be similar to our logo design with some nice texture or abstract shapes thrown in.
Pricelist, contact details and logo is attached
I would prefer it to be a 3 fold brochure.

Target Market(s)

Females aged 30-50

Colors
85acd3
cedeed
c4c4c4
5c5c5c
000000
ffffff
eea3c7
f9d9e8
dbdbdb

Requirements
Must have
• easy to read

```html
<!DOCTYPE html>
<html lang="en">
<head>
<meta charset="utf-8">
<title>Willow Skin Clinic – Price List</title>
<link href="https://fonts.googleapis.com/css2?family=Mukta:wght@300;700&display=swap" rel="stylesheet">
<style>
:root{
  --ink:#56626f;
  --panel:#56616d;
  --paper:#ffffff;
  --photo-warm-a:#d9c2b6;
  --photo-warm-b:#8d8f95;
  --photo-cool-a:#cfd6dd;
  --photo-cool-b:#6e6f74;
  --petal-a:#e6e9ec;
  --petal-b:#9aa3ad;
}
*{margin:0;padding:0;box-sizing:border-box}
html,body{width:1200px;height:927px;overflow:hidden;background:var(--paper)}
.brochure{position:relative;width:1200px;height:927px;font-family:"Mukta",sans-serif;font-weight:300;color:var(--ink);font-size:17.5px;line-height:21.6px;letter-spacing:-0.4px}
.panel{position:absolute;top:0;height:927px}
.panel--left{left:0;width:400px;background:var(--paper)}
.panel--middle{left:400px;width:400px;background:var(--panel);color:var(--paper)}
.panel--right{left:800px;width:400px;background:var(--paper)}
.price-block{position:absolute;text-align:center;white-space:nowrap}
.price-block b{font-weight:700}
.gap{height:21.6px}
.gap--double{height:43.2px}
.hair-removal{left:5px;width:200px;top:57px}
.rejuvenation{left:167px;width:220px;top:57px}
.middle-list{left:0;width:400px;top:123px}
.right-list{left:0;width:400px;top:325px}
.photo{position:absolute}
.photo--treatment{left:0;top:614px;width:400px;height:271px;background:linear-gradient(135deg,var(--photo-cool-a),var(--photo-cool-b))}
.photo--injection{left:0;top:34px;width:400px;height:271px;background:linear-gradient(135deg,var(--photo-warm-b),var(--photo-warm-a))}
.petal{position:absolute;border-radius:50%;background:radial-gradient(circle,var(--petal-a),var(--petal-b));opacity:.8}
.petal--top{left:78px;top:-40px;width:205px;height:108px}
.petal--bottom{left:123px;top:830px;width:160px;height:140px}
</style>
</head>
<body>
<main class="brochure">
  <section class="panel panel--left">
    <div class="price-block hair-removal">
      <b>IPL hair removal</b><br>Upper lip $50<br>Chin $50<br>Cheeks $75<br>Whole face $350
      <div class="gap"></div>
      Bikini $90<br>G String $120<br>Brazilian $150
      <div class="gap"></div>
      Underarms $90<br>Half arm $180<br>Full arm $250<br>Half leg $290<br>Thighs $290<br>Full leg $490
      <div class="gap"></div>
      Full back $350<br>Shoulders $180<br>Nipples $60<br>Snail trail $50<br>Stomach $250<br>Chest $250<br>Buttocks $200
    </div>
    <div class="price-block rejuvenation">
      <b>IPL Photo Rejuvenation</b><br>Full face $350<br>Neck $200<br>Face, neck ad décolletage<br>$450<br>Spot Treatment $50<br>Waxing<br>Eyebrow $21<br>Lip $15<br>Chin $15<br>Sides of face $20<br>Underarm $20<br>Forearm $25<br>Full arm $35<br>Lower leg $30<br>Upper leg $30<br>Full leg $50<br>Inner thigh $10<br>Snail trail $10<br>Bikini $30<br>G String $40<br>Brazilian $50
    </div>
    <div class="photo photo--treatment" role="img" aria-label="Photo of a client receiving a facial device treatment"></div>
  </section>

  <section class="panel panel--middle">
    <div class="petal petal--top" role="img" aria-label="Soft grey floral decoration"></div>
    <div class="price-block middle-list">
      Eyebrow wax and Lip wax $30<br>Eyebrow, lip and chin wax $45
      <div class="gap"></div>
      <b>Mens waxing</b><br>Mono brow $5<br>Eyebrow $21<br>Neck $20<br>Full back $45<br>Chest and Abdomen $45
      <div class="gap"></div>
      <b>Tinting</b><br>Eyelash Tint $25<br>Lash Lift and Tint $80
      <div class="gap"></div>
      Henna eyebrows and wax $80<br>Eyelash Tint and brow wax $40
      <div class="gap"></div>
      <b>Willow Mini Facial</b>&nbsp; $80 &nbsp; 40min
      <div class="gap"></div>
      <b>Willow Deluxe Facial</b>&nbsp;&nbsp; $110 &nbsp; 1 hour
      <div class="gap"></div>
      <b>Microdermabrasion</b>&nbsp; $125
      <div class="gap"></div>
      <b>Mini Micro</b> $80
      <div class="gap"></div>
      <b>Wrinkle Relaxers</b> $175 per area (Crows,<br>frown lines, forehead lines) or all 3 areas for<br>$450<br>$50 minor areas (Gummy smile, brow lift,<br>bunny lines)
      <div class="gap"></div>
      <b>Dermal Fillers and Lip Fillers</b> $500 per ml
    </div>
    <div class="petal petal--bottom" role="img" aria-label="Soft grey floral decoration"></div>
  </section>

  <section class="panel panel--right">
    <div class="photo photo--injection" role="img" aria-label="Photo of a practitioner giving a client a cosmetic injection"></div>
    <div class="price-block right-list">
      <b>Chemical Peels</b><br><b>Aurelle Peels</b> 30min<br>Lactic Acid Peels 20%/40%/60%&nbsp; $120<br>Anti-Ageing Peel&nbsp; $120<br>Even Tone Peel $120<br>Clear Skin Peel&nbsp; $120
      <div class="gap"></div>
      <b>Solvene Peels</b>&nbsp; 30min<br>Berry Enzyme Peel $120<br>Fruit Enzyme Peel $120<br>Radiance Peel $120<br>Retinol Renewal Peel $250
      <div class="gap--double"></div>
      <b>Lumora LED</b><br>$90 per treatment &nbsp; or<br>$50 when added on to any of our other<br>skin treatments.
      <div class="gap"></div>
      <b>Velanne Microneedlin</b>g (Collagen<br>Induction Therapy)<br>$350 full face<br>$450 face, neck and décolletage
      <div class="gap"></div>
      <b>Sorielle Laser Facial</b><br>$350 full face<br>$450 face, neck and décolletage
    </div>
  </section>
</main>
</body>
</html>
```